Automotive eCommerce Business looking for a business card design

Looking for a clean and simple business card design. Our company name is "Brindle Auto" and we are a company specializing in the ecommerce sales of automotive parts, specifically for pick up trucks and large SUVs. Our company colours are red, black, and white.

Feel free to use the logo provided or create a new logo that you seem fit. Looking forward to your creative ideas!

Industry/Entity Type

Automotive

Contact Information for Business Card

We were thinking of a possibly two-sided design featuring just the logo and company name on one side, and personal information on the other side. Single sided designs will be considered as well.

Font styles to use
Serif
Sans Serif
Decorative

Colors
ec1f27
ffffff
000000

Requirements
Must have
• Space for employee's name, title, phone number and email address, along with the company address and website somewhere.

```html
<!DOCTYPE html>
<html lang="en">
<head>
<meta charset="utf-8">
<title>Brindle Auto Ltd. – Business Card</title>
<link rel="stylesheet" href="https://fonts.googleapis.com/css2?family=Cinzel:wght@500&family=Roboto:wght@400;500;700&display=swap">
<style>
  :root {
    --stage: #2b2b2b;
    --paper: #f2f2f2;
    --brand-red: #991d21;
    --slate: #4a4e4f;
    --ink-grey: #555555;
    --white: #ffffff;
    --serif: "Cinzel", serif;
    --sans: "Roboto", sans-serif;
  }
  * { box-sizing: border-box; margin: 0; padding: 0; }
  html, body { width: 1200px; height: 960px; overflow: hidden; }
  body { background: var(--stage); position: relative; font-family: var(--sans); }

  .card {
    position: absolute;
    width: 600px;
    height: 343px;
    overflow: hidden;
  }
  .card--front { left: 314px; top: 113px; background: var(--paper); }
  .card--back  { left: 311px; top: 472px; background: var(--slate); }

  .front__panel { position: absolute; inset: 0; }

  .brand-block {
    position: absolute;
    left: 145px;
    transform: translateX(-50%);
    display: flex;
    flex-direction: column;
    align-items: center;
  }
  .card--front .brand-block { top: 100px; }
  .brand-mark {
    width: 86px; height: 86px;
    background: var(--brand-red);
    border-radius: 6px;
  }
  .brand-name {
    font-family: var(--serif);
    font-weight: 500;
    white-space: nowrap;
    letter-spacing: 0.5px;
  }
  .card--front .brand-name { margin-top: 40px; font-size: 21px; color: var(--ink-grey); }

  .contact {
    position: absolute;
    left: 446px; top: 68px;
    transform: translateX(-50%);
    text-align: center;
    color: var(--white);
    white-space: nowrap;
  }
  .contact__name { font-size: 20px; font-weight: 700; line-height: 26px; }
  .contact__title { font-size: 15px; font-weight: 500; line-height: 20px; }
  .contact__address { margin-top: 14px; font-size: 14.5px; line-height: 19px; }
  .contact__lines { margin-top: 10px; list-style: none; font-size: 14.5px; line-height: 19.3px; }
  .contact__lines li { display: flex; align-items: center; justify-content: center; gap: 5px; }
  .icon { width: 12px; height: 12px; fill: var(--white); flex: none; }

  .card--back .brand-block { left: 300px; top: 68px; }
  .card--back .brand-mark { width: 150px; height: 150px; background: var(--paper); border-radius: 10px; }
  .card--back .brand-name { margin-top: 22px; font-size: 26px; color: var(--paper); }
  .back__web {
    position: absolute;
    left: 0; right: 0; top: 290px;
    text-align: center;
    font-size: 14px;
    letter-spacing: 5px;
    color: var(--paper);
  }
</style>
</head>
<body>

<section class="card card--front" aria-label="Business card, front">
  <svg class="front__panel" viewBox="0 0 600 343" width="600" height="343" aria-hidden="true">
    <path d="M421 0 H600 V343 H436 Q420 343 405 333 L296 262 Q282 252 282 236 V106 Q282 90 296 82 L400 8 Q410 0 421 0 Z" fill="var(--brand-red)"/>
  </svg>

  <div class="brand-block">
    <div class="brand-mark"></div>
    <div class="brand-name">Brindle Auto Ltd.</div>
  </div>

  <div class="contact">
    <div class="contact__name">OWEN HARTLEY</div>
    <div class="contact__title">CEO/FOUNDER</div>
    <div class="contact__address">2140 Larkspur Road<br>Fairbanks, Alaska 34812</div>
    <ul class="contact__lines">
      <li><svg class="icon" viewBox="0 0 24 24"><path d="M6.6 10.8a15 15 0 0 0 6.6 6.6l2.2-2.2a1 1 0 0 1 1-.25 11 11 0 0 0 3.6.6 1 1 0 0 1 1 1V20a1 1 0 0 1-1 1A17 17 0 0 1 3 4a1 1 0 0 1 1-1h3.5a1 1 0 0 1 1 1c0 1.25.2 2.45.6 3.6a1 1 0 0 1-.25 1z"/></svg>555 014 2538</li>
      <li><svg class="icon" viewBox="0 0 24 24"><path d="M7 1h10a2 2 0 0 1 2 2v18a2 2 0 0 1-2 2H7a2 2 0 0 1-2-2V3a2 2 0 0 1 2-2zm0 3v14h10V4z"/></svg>555 018 9364</li>
      <li><svg class="icon" viewBox="0 0 24 24"><path d="M6 2h12v6H6zM3 9h18a1 1 0 0 1 1 1v8h-4v4H6v-4H2v-8a1 1 0 0 1 1-1zm5 7v4h8v-4z"/></svg>555 016 1940</li>
      <li><svg class="icon" viewBox="0 0 24 24"><path d="M2 5h20v14H2zm2 2v.5l8 5 8-5V7l-8 5z"/></svg>owen@brindleauto.com</li>
      <li><svg class="icon" viewBox="0 0 24 24"><circle cx="12" cy="12" r="10"/></svg>www.brindleauto.com</li>
    </ul>
  </div>
</section>

<section class="card card--back" aria-label="Business card, back">
  <div class="brand-block">
    <div class="brand-mark"></div>
    <div class="brand-name">Brindle Auto Ltd.</div>
  </div>
  <div class="back__web">www.brindleauto.com</div>
</section>

</body>
</html>
```